UK landscaping company needs website

We, Brackwell Landscapes need a website design for a company based in Surrey, UK. The design should be bold and playful. We have three main areas of work driveways, paving and fencing. It shouldn't be too heavy in text and concentrate on the pictures from previous jobs we've completed. You may use stock images for the design, these can be changed if you are successful. Please don’t just copy the flyer it is just there to provide content.
We have a logo design which we would also like editing slightly.
Here are some of my local competitors
https://www.pelmarlandscapes.example.co.uk/

https://www.twinfirgardendesign.example.com/

https://kestbyrnlandscapes.example.co.uk/

Industry/Entity Type

Landscaping

Coding

Coded - Design and coding required

Number of Pages Required

3 page

Font styles to use
Sans Serif

Requirements
Must have
• Pictures of my previous jobs.
Must be mobile friendly
Easy to navigate
Nice to have
• Try to use different colours. It would be good to have some designs that aren’t just black and green.
I’d like some curves in the design.
Should not have
• We install hard landscaping. Think more building/construction and less plants and cutting grass.

```html
<!DOCTYPE html>
<html lang="en">
<head>
<meta charset="utf-8">
<title>Brackwell Landscapes</title>
<link href="https://fonts.googleapis.com/css2?family=Rubik:wght@400;500;700&display=swap" rel="stylesheet">
<style>
:root{
  --green:#52b52b;
  --green-dark:#3f9a1f;
  --ink:#231f1e;
  --panel:#2b2725;
  --dark-band:#3b3431;
  --grey-bg:#efefef;
  --text:#3a3a3a;
  --muted:#cfc9c6;
  --white:#ffffff;
  --star:#f5a623;
}
*{margin:0;padding:0;box-sizing:border-box}
html,body{width:1200px;height:4184px;overflow:hidden}
body{position:relative;font-family:"Rubik",Arial,sans-serif;color:var(--text);background:var(--white)}

/* header */
.site-header{position:absolute;left:0;top:0;width:1200px;height:72px;background:var(--panel);z-index:5}
.brand{position:absolute;left:130px;top:18px;display:flex;align-items:center;gap:10px;color:var(--white);font-weight:700;font-size:30px;letter-spacing:1px}
.brand-dot{width:12px;height:12px;border-radius:50%;background:var(--green)}
.main-nav a{position:absolute;top:28px;color:var(--white);font-size:15px;font-weight:500;text-decoration:none}
.header-cta{position:absolute;right:0;top:0;width:201px;height:72px;background:var(--green);color:var(--white);padding:14px 0 0 28px}
.header-cta small{display:block;font-size:13px;font-weight:500}
.header-cta strong{display:block;font-size:22px;font-weight:500;margin-top:1px}

/* hero */
.hero-photo{position:absolute;left:0;top:72px;width:1200px;height:840px;
  background:linear-gradient(160deg,#5d4a34 0%,#7b5a3f 25%,#9a948b 50%,#b7b3ab 65%,#4f6f2c 100%)}
.hero-shade{position:absolute;left:0;top:72px;width:760px;height:600px;background:linear-gradient(90deg,rgba(20,18,16,.6),rgba(20,18,16,0))}
.hero-title{position:absolute;left:130px;top:208px;width:620px;color:var(--white);font-size:52px;font-weight:700;line-height:58px;letter-spacing:-.5px;white-space:nowrap}
.hero-points{position:absolute;left:132px;top:404px;list-style:none;color:var(--white);font-size:20px}
.hero-points li{display:flex;align-items:center;gap:12px;height:37px}
.btn{display:inline-flex;align-items:center;gap:10px;background:var(--green);color:var(--white);font-weight:500;font-size:16px;text-decoration:none}
.hero-btn{position:absolute;left:131px;top:541px;width:189px;height:49px;justify-content:center}
.hero-curve{position:absolute;left:0;top:600px}

/* estimate form */
.estimate{position:absolute;left:607px;top:573px;width:458px;height:538px;background:var(--panel);box-shadow:0 8px 24px rgba(0,0,0,.3);z-index:3}
.estimate h2{position:absolute;left:0;top:38px;width:100%;text-align:center;color:var(--white);font-size:24px;font-weight:500}
.estimate p{position:absolute;left:70px;top:70px;width:318px;text-align:center;color:var(--muted);font-size:14px;line-height:20px}
.field{position:absolute;height:37px;border:1px solid #4a4442;background:#2f2a28;color:var(--white);font-size:12px;font-weight:500;padding:12px 16px}
.field-select-arrow{position:absolute;right:0;top:0;width:44px;height:35px;background:var(--green)}
.estimate .btn{position:absolute;left:192px;top:426px;width:242px;height:45px;justify-content:center;font-size:16px}

/* about */
.about h2{position:absolute;left:130px;top:898px;font-size:44px;font-weight:700;color:var(--ink)}
.accent{color:var(--green)}
.about p{position:absolute;left:130px;top:966px;width:445px;font-size:16.5px;line-height:24px;color:#444}

/* services */
.section-title{position:absolute;left:0;width:1200px;text-align:center;font-size:46px;font-weight:700;color:var(--ink)}
.services-band{position:absolute;left:0;top:1420px}
.service{position:absolute;border-radius:50%;border:7px solid var(--white);display:flex;align-items:flex-end;justify-content:center;color:var(--white);font-size:26px;font-weight:500;box-shadow:0 0 0 16px var(--green)}
.service span{margin-bottom:62px}
.why-title{position:absolute;left:0;top:1772px;width:1200px;text-align:center;color:var(--white);font-size:44px;font-weight:700}
.why-rule{position:absolute;left:572px;top:1832px;width:56px;height:3px;background:var(--green)}
.why-lede{position:absolute;left:240px;top:1850px;width:720px;text-align:center;color:var(--muted);font-size:17px;line-height:30px}
.feature{position:absolute;top:1939px;width:220px;text-align:center;color:var(--white)}
.feature-icon{width:94px;height:94px;margin:0 auto;border:2px solid var(--white);border-radius:50%;display:flex;align-items:center;justify-content:center}
.feature h3{margin-top:20px;font-size:22px;font-weight:400}
.feature p{margin-top:10px;font-size:13px;line-height:19px;color:var(--muted);padding:0 14px}

/* latest work */
.work-tile{position:absolute}
.work-more{position:absolute;left:447px;top:2718px;width:302px;height:270px;background:linear-gradient(160deg,#6fc64a,#4fae2b);display:flex;flex-direction:column;align-items:center;justify-content:center;color:var(--white);font-size:28px;font-weight:500;gap:22px}
.work-more i{width:42px;height:42px;border-radius:50%;background:var(--white);display:flex;align-items:center;justify-content:center}

/* process */
.process{position:absolute;left:0;top:3085px;width:1200px;height:485px;background:var(--grey-bg)}
.eyebrow{position:absolute;left:130px;top:87px;color:var(--green);font-size:15px;font-weight:700}
.process h2{position:absolute;left:130px;top:112px;width:420px;font-size:34px;line-height:39px;font-weight:700;color:var(--ink)}
.process .lede{position:absolute;left:130px;top:250px;width:400px;font-size:14.5px;line-height:24px;color:#333}
.step{position:absolute;left:607px;width:466px}
.step-icon{position:absolute;left:0;top:0;width:54px;height:50px;display:flex;align-items:center;justify-content:center;background:#3a3f49}
.step-icon.active{background:var(--green)}
.step-label{position:absolute;left:73px;top:6px;font-size:13px;color:#444}
.step h3{position:absolute;left:73px;top:20px;font-size:22px;font-weight:700;color:var(--ink)}
.step-line{position:absolute;left:73px;top:49px;width:393px;height:1px;background:#9a9a9a}
.step-toggle{position:absolute;right:6px;top:14px;color:var(--green);font-size:26px;line-height:20px;font-weight:400}
.step p{position:absolute;left:73px;top:72px;width:380px;font-size:13px;line-height:21px;color:#333}

/* testimonial */
.arrow-btn{position:absolute;top:3657px;width:40px;height:40px;border-radius:50%;display:flex;align-items:center;justify-content:center}
.arrow-btn.outline{border:2px solid var(--green)}
.arrow-btn.solid{background:var(--green)}
.client-photo{position:absolute;left:310px;top:3634px;width:109px;height:101px;background:linear-gradient(135deg,#c9b6a2,#e6d8c8)}
.client-badge{position:absolute;left:398px;top:3719px;width:20px;height:20px;background:var(--green);border:2px solid var(--white)}
.quote{position:absolute;left:434px;top:3638px;width:460px;font-size:14px;line-height:21px;color:#222}
.review-meta{position:absolute;left:434px;top:3714px;font-size:13px;font-weight:700;color:#222;display:flex;gap:14px;align-items:center}
.stars{color:var(--star);letter-spacing:3px;font-size:13px}

/* footer */
.site-footer{position:absolute;left:0;top:3820px;width:1200px;height:364px;background:var(--panel);color:var(--white)}
.footer-brand{position:absolute;left:132px;top:108px;display:flex;align-items:center;gap:10px;font-size:31px;font-weight:700;letter-spacing:.5px;white-space:nowrap}
.footer-brand i{width:12px;height:12px;border-radius:50%;background:var(--green)}
.footer-col{position:absolute;top:80px;list-style:none}
.footer-col li{height:28px;font-size:12px}
.footer-col li.head{font-size:14px;font-weight:500;height:34px}
.footer-col a{color:var(--white)}
.footer-col.plain li{font-size:14px;font-weight:500;height:36px}
.footer-map{position:absolute;left:786px;top:82px;width:281px;height:106px;background:linear-gradient(135deg,#dfe6ee,#cfdce9);border-bottom:4px solid #f0c14b}
.socials{position:absolute;left:525px;top:240px;display:flex;gap:7px}
.socials i{width:32px;height:32px;border-radius:50%;border:1.5px solid #bdb6b2}
.footer-rule{position:absolute;left:28px;top:297px;width:1144px;height:1px;background:#4a4543}
.copyright{position:absolute;left:0;top:318px;width:1200px;text-align:center;font-size:14px;color:#d8d3d0}
</style>
</head>
<body>

<header class="site-header">
  <div class="brand"><span class="brand-dot"></span>BRACKWELL</div>
  <nav class="main-nav">
    <a style="left:475px">HOME</a>
    <a style="left:563px">SERVICES</a>
    <a style="left:680px">ABOUT</a>
    <a style="left:774px">OUR WORK</a>
    <a style="left:899px">CONTACT</a>
  </nav>
  <div class="header-cta"><small>FREE ESTIMATES</small><strong>079 0061 4482</strong></div>
</header>

<section class="hero">
  <div class="hero-photo" role="img" aria-label="Photo of a finished garden with grey paving slabs, lawn, timber pergola and brick walls"></div>
  <div class="hero-shade"></div>
  <h1 class="hero-title">Your garden and<br>driveway cared for<br>the way they should be</h1>
  <ul class="hero-points">
    <li><svg width="24" height="24" viewBox="0 0 24 24" fill="none" stroke="#fff" stroke-width="1.8"><path d="M20 10.5A9 9 0 1 1 15 4"/><path d="M7 11l4 4 10-10"/></svg>25 years combined experience</li>
    <li><svg width="24" height="24" viewBox="0 0 24 24" fill="none" stroke="#fff" stroke-width="1.8"><path d="M20 10.5A9 9 0 1 1 15 4"/><path d="M7 11l4 4 10-10"/></svg>Extraordinary driveway and garden installation</li>
    <li><svg width="24" height="24" viewBox="0 0 24 24" fill="none" stroke="#fff" stroke-width="1.8"><path d="M20 10.5A9 9 0 1 1 15 4"/><path d="M7 11l4 4 10-10"/></svg>Quality that is guaranteed</li>
  </ul>
  <a class="btn hero-btn">GET STARTED <svg width="18" height="18" viewBox="0 0 18 18"><circle cx="9" cy="9" r="8" fill="#fff"/><path d="M7.5 5.5L11 9l-3.5 3.5" stroke="#52b52b" stroke-width="2" fill="none"/></svg></a>
  <svg class="hero-curve" width="1200" height="340" viewBox="0 0 1200 340">
    <path d="M0 300 C 250 150, 600 90, 1200 100 L1200 130 C 650 120, 300 170, 0 330 Z" fill="#52b52b"/>
    <path d="M0 330 C 300 170, 650 120, 1200 130 L1200 340 L0 340 Z" fill="#fff"/>
  </svg>
</section>

<form class="estimate">
  <h2>GET A FREE ESTIMATE</h2>
  <p>Fill out out form below and a representative will be in touch.</p>
  <div class="field" style="left:25px;top:137px;width:196px">NAME</div>
  <div class="field" style="left:238px;top:137px;width:196px">PHONE</div>
  <div class="field" style="left:25px;top:190px;width:196px">EMAIL</div>
  <div class="field" style="left:238px;top:190px;width:196px">ADDRESS</div>
  <div class="field" style="left:25px;top:245px;width:409px">ESTIMATE TYPE
    <span class="field-select-arrow"><svg width="44" height="35" viewBox="0 0 44 35"><path d="M17 15l5 6 5-6z" fill="#fff"/></svg></span></div>
  <div class="field" style="left:25px;top:299px;width:409px;height:109px">HOW CAN WE HELP ?</div>
  <a class="btn">START MY ESTIMATE <svg width="18" height="18" viewBox="0 0 18 18"><circle cx="9" cy="9" r="8" fill="#fff"/><path d="M7.5 5.5L11 9l-3.5 3.5" stroke="#52b52b" stroke-width="2" fill="none"/></svg></a>
</form>

<section class="about">
  <h2>ABOUT <span class="accent">BRACKWELL</span></h2>
  <p>Lorem Ipsum is simply dummy text of the printing and typesetting industry. Lorem Ipsum has industry's standard dummy text ever since the 1500s, when an unknown printer took a galley of type and scrambled Lorem Ipsum is simply dummy text of the printing and typesetting industry.</p>
</section>

<h2 class="section-title" style="top:1236px">OUR <span class="accent">SERVICES</span></h2>

<section>
  <svg class="services-band" width="1200" height="860" viewBox="0 0 1200 860">
    <path d="M0 240 C 350 60, 800 40, 1200 95 L1200 125 C 800 80, 350 100, 0 260 Z" fill="#52b52b"/>
    <defs><linearGradient id="bandFill" x1="0" y1="0" x2="1" y2="1"><stop offset="0" stop-color="#3d3532"/><stop offset=".6" stop-color="#332d2a"/><stop offset="1" stop-color="#3b4a2a"/></linearGradient></defs>
    <path d="M0 260 C 350 100, 800 80, 1200 125 L1200 855 L0 855 Z" fill="url(#bandFill)" role="img" aria-label="Photo of timber fence panels above a lawn"/>
  </svg>
  <div class="service" style="left:164px;top:1380px;width:276px;height:276px;background:linear-gradient(180deg,#b9b7b2,#4d4e5c 60%,#3b3d4c)" role="img" aria-label="Photo of a block paved driveway"><span>DRIVEWAYS</span></div>
  <div class="service" style="left:762px;top:1367px;width:286px;height:286px;background:linear-gradient(180deg,#c9a978,#8a8d55 55%,#4e8b2c)" role="img" aria-label="Photo of timber decking beside artificial grass"><span>FENCING</span></div>
  <div class="service" style="left:429px;top:1348px;width:340px;height:340px;background:linear-gradient(180deg,#7a6a58,#38a8d8 40%,#b59a7c 65%,#8f7a62)" role="img" aria-label="Photo of a swimming pool surrounded by stone paving"><span style="margin-bottom:72px">PAVING</span></div>

  <h2 class="why-title">WHY CHOOSE US?</h2>
  <div class="why-rule"></div>
  <p class="why-lede">Lorem Ipsum is simply dummy text of the printing and typesetting industry. Lorem Ipsum hasindustry's standard dummy text</p>

  <div class="feature" style="left:202px">
    <div class="feature-icon"><svg width="46" height="46" viewBox="0 0 46 46"><circle cx="27" cy="18" r="12" fill="#52b52b"/><circle cx="27" cy="18" r="5" fill="none" stroke="#fff" stroke-width="2"/><path d="M18 27L6 39" stroke="#52b52b" stroke-width="5" stroke-linecap="round"/></svg></div>
    <h3>Professionalism</h3>
    <p>Use our body field scanner, at home to uncover why yhou feelthe way you do</p>
  </div>
  <div class="feature" style="left:497px">
    <div class="feature-icon"><svg width="50" height="50" viewBox="0 0 50 50"><circle cx="25" cy="25" r="21" fill="#52b52b"/><path d="M15 25l7 7 16-16" stroke="#fff" stroke-width="4" fill="none"/></svg></div>
    <h3>Better Results</h3>
    <p>Use our body field scanner, at home to uncover why yhou feelthe way you do</p>
  </div>
  <div class="feature" style="left:778px">
    <div class="feature-icon"><svg width="50" height="50" viewBox="0 0 50 50" fill="none" stroke="#52b52b" stroke-width="3"><circle cx="12" cy="12" r="4" fill="#52b52b"/><circle cx="38" cy="25" r="4" fill="#52b52b"/><circle cx="12" cy="38" r="4" fill="#52b52b"/><path d="M16 12h18a6 6 0 0 1 0 13M34 25H16a6 6 0 0 0 0 13h24" stroke-dasharray="4 3"/></svg></div>
    <h3>Quality Work</h3>
    <p>Use our body field scanner, at home to uncover why yhou feelthe way you do</p>
  </div>
</section>

<section class="latest-work">
  <h2 class="section-title" style="top:2341px">LATEST <span class="accent">WORK</span></h2>
  <div class="work-tile" style="left:136px;top:2439px;width:457px;height:270px;background:linear-gradient(120deg,#6b5a44,#5aa238 40%,#9c9890 70%,#d8d6d0)" role="img" aria-label="Photo of a lawn with stone paving and timber steps"></div>
  <div class="work-tile" style="left:602px;top:2439px;width:457px;height:270px;background:linear-gradient(170deg,#d9dadf,#a3a4a8 35%,#8c7466 60%,#756052)" role="img" aria-label="Photo of a curved block paved driveway"></div>
  <div class="work-tile" style="left:136px;top:2718px;width:302px;height:270px;background:linear-gradient(180deg,#6d5a45,#5c9c32 50%,#a67a4c 80%,#b7b2aa)" role="img" aria-label="Photo of timber sleeper steps and lawn"></div>
  <div class="work-more">
    <i><svg width="18" height="18" viewBox="0 0 18 18" fill="none" stroke="#555" stroke-width="1.6"><path d="M4 14L14 4M8 4h6v6"/></svg></i>
    View More
  </div>
  <div class="work-tile" style="left:757px;top:2718px;width:302px;height:270px;background:linear-gradient(180deg,#8ca6c0,#7b6446 35%,#a3804f 70%,#4f9a2c)" role="img" aria-label="Photo of a new timber fence beside a lawn"></div>
</section>

<section class="process">
  <div class="eyebrow">OUR PROCESS</div>
  <h2>A COMPANY YOU CAN TRUST TO BE WITH YOU AT EVERY STEP</h2>
  <p class="lede">Lorem Ipsum is simply dummy text of the printing and typesetting industry. Lorem Ipsum has been the industry's standard dummy text ever since the 1500s, when an unknown printer took.</p>

  <div class="step" style="top:83px">
    <div class="step-icon active"><svg width="28" height="28" viewBox="0 0 28 28" fill="none" stroke="#fff" stroke-width="2"><path d="M5 23l4-1 13-13-3-3L6 19z"/><path d="M17 8l3 3"/></svg></div>
    <span class="step-label">STEP 1</span>
    <h3>CONTACT</h3>
    <span class="step-toggle">×</span>
    <div class="step-line"></div>
    <p>Fill out our contact form or give us a call to beging your FREE service estimate. Lorem Ipsum is simply dummy text of the printing and typesetting industry. Lorem Ipsum has been the industry's standard dummy text ever since the 1500s.</p>
  </div>
  <div class="step" style="top:270px">
    <div class="step-icon"><svg width="26" height="28" viewBox="0 0 26 28" fill="none" stroke="#fff" stroke-width="1.8"><path d="M5 3h11l5 5v17H5z"/><path d="M9 12h8M9 16h8M9 20h6"/></svg></div>
    <span class="step-label">STEP 2</span>
    <h3>PROPOSAL</h3>
    <span class="step-toggle">+</span>
    <div class="step-line"></div>
  </div>
  <div class="step" style="top:343px">
    <div class="step-icon"><svg width="28" height="28" viewBox="0 0 28 28" fill="none" stroke="#fff" stroke-width="1.8"><path d="M4 24h20M6 24V12l8-6 8 6v12M11 24v-6h6v6"/></svg></div>
    <span class="step-label">STEP3</span>
    <h3>CONSTRUCTION</h3>
    <span class="step-toggle">+</span>
    <div class="step-line"></div>
  </div>
</section>

<section class="testimonial">
  <span class="arrow-btn outline" style="left:198px"><svg width="14" height="14" viewBox="0 0 14 14"><path d="M9 2L4 7l5 5" stroke="#52b52b" stroke-width="1.8" fill="none"/></svg></span>
  <span class="arrow-btn solid" style="left:962px"><svg width="14" height="14" viewBox="0 0 14 14"><path d="M5 2l5 5-5 5" stroke="#fff" stroke-width="1.8" fill="none"/></svg></span>
  <div class="client-photo" role="img" aria-label="Photo of a happy customer couple"></div>
  <div class="client-badge"></div>
  <p class="quote">“They did an excellent job. It great! It only took on day, and the installers did and excellent job cleaning up....I highly recommend them if you went a professional job done right”</p>
  <div class="review-meta"><span>CUSTOMER NAME</span><span>|</span><span>VERIFIED REVIEW</span><span>|</span><span class="stars">★★★★★</span></div>
</section>

<footer class="site-footer">
  <div class="footer-brand"><i></i>BRACKWELL</div>
  <ul class="footer-col plain" style="left:385px;top:82px"><li>HOME</li><li>ABOUT US</li><li>OUR WORK</li><li>CONTACT</li></ul>
  <ul class="footer-col" style="left:505px"><li class="head">SERVICES</li><li><a>Driveways</a></li><li><a>Paving</a></li><li><a>Fencing</a></li></ul>
  <ul class="footer-col" style="left:633px"><li class="head">QUICK LINKS</li><li><a>FAQ</a></li><li><a>Testimonials</a></li><li><a>Sitemap</a></li></ul>
  <div class="footer-map" role="img" aria-label="Map showing the company location with a red pin"></div>
  <div class="socials"><i></i><i></i><i></i><i></i></div>
  <div class="footer-rule"></div>
  <p class="copyright">© 2020 Brackwell Landscapes. All Rights are Reserved.</p>
</footer>

</body>
</html>
```